New Bicycle shop business card

Hi!
I'm looking for a business card for my new proffesional bike mechanics shop. This shop is only for fixing broken bikes and not selling bikes.
Peferbly a modern and sleek and modern design.
Colors: black, grey, red, white
Information:
Name: Rijwielwerkplaats Vanhoutte
Shop owner: Bart Vanhoutte & Marieke Segers
Website: www.rijwielwerkplaats-vanhoutte.be
Email: info@rijwielwerkplaats-vanhoutte.be
Phone number: +32471902368
Street adres: Kerkweg 46
9940 Bellebeke
Slogan/shop information: Herstellingen van alle merken.
Logo: see files.
Target Market(s)
People who seek a mechanic to fix or upgrade their bikes.
Contact Information for Business Card
Information:
Website: info@rijwielwerkplaats-vanhoutte.be
9940 Bellebeke
Logo: see files.

```html
<!DOCTYPE html>
<html lang="nl">
<head>
<meta charset="utf-8">
<title>Rijwielwerkplaats Vanhoutte – Business Card</title>
<link href="https://fonts.googleapis.com/css2?family=Open+Sans:ital,wght@0,400;0,600;0,700;0,800;1,400&display=swap" rel="stylesheet">
<style>
  :root {
    --backdrop: #3b3532;
    --card-black: #0b0b0c;
    --card-white: #ffffff;
    --brand-red: #e8243f;
    --brand-grey: #8f8f8f;
    --text-dark: #1a1a1a;
    --text-light: #ffffff;
  }
  * { box-sizing: border-box; margin: 0; padding: 0; }
  html, body {
    width: 1200px; height: 716px; overflow: hidden;
    background: var(--backdrop);
    font-family: "Open Sans", Arial, sans-serif;
  }
  .stage {
    position: relative; width: 1200px; height: 716px;
    display: flex; align-items: center; justify-content: center; gap: 40px;
  }
  .card {
    position: relative; width: 540px; height: 310px;
    box-shadow: 0 14px 30px rgba(0,0,0,.45);
    overflow: hidden;
  }

  /* Front */
  .card--front { background: var(--card-black); }
  .front-pattern {
    position: absolute; inset: 0;
    background: radial-gradient(ellipse at 50% 45%, #141415 0%, #0b0b0c 70%);
  }
  .front-identity {
    position: absolute; inset: 0;
    display: flex; flex-direction: column; align-items: center; justify-content: center;
  }
  .wordmark {
    display: flex; align-items: center; gap: 12px;
  }
  .wordmark__square { width: 22px; height: 22px; background: var(--brand-red); }
  .wordmark__name {
    color: var(--text-light); font-weight: 800; font-size: 22px;
    letter-spacing: 1.5px; text-transform: uppercase; line-height: 1.15;
    text-align: left;
  }
  .slogan {
    margin-top: 30px; color: var(--text-light); font-size: 13px;
  }

  /* Back */
  .card--back { background: var(--card-white); }
  .owners { position: absolute; left: 52px; top: 40px; }
  .owners__label { color: var(--brand-red); font-size: 13px; font-weight: 600; }
  .owners__names { color: var(--brand-grey); font-size: 15px; font-weight: 700; margin-top: 1px; }

  .accent-bar {
    position: absolute; left: 0; top: 104px; width: 22px; height: 36px;
    background: var(--brand-red);
  }
  .company { position: absolute; left: 36px; top: 104px; }
  .company__name { color: var(--brand-red); font-size: 16px; font-weight: 700; line-height: 1.2; }
  .company__role { color: var(--text-dark); font-size: 11.5px; font-weight: 600; margin-top: 1px; }

  .contact { position: absolute; left: 36px; top: 168px; list-style: none; }
  .contact__item {
    display: flex; align-items: center; gap: 8px;
    color: var(--brand-grey); font-size: 12px; line-height: 19px;
  }
  .contact__icon { width: 11px; height: 11px; flex: none; }
  .address { position: absolute; left: 36px; top: 236px; color: var(--brand-grey); font-size: 12px; }

  .back-mark {
    position: absolute; right: 28px; bottom: 40px; width: 150px;
    display: flex; flex-direction: column; align-items: flex-start; gap: 10px;
  }
  .back-mark__square { width: 64px; height: 64px; background: var(--brand-red); }
  .back-mark__name { color: var(--text-dark); font-size: 15px; font-weight: 800; line-height: 1.2; }
</style>
</head>
<body>
<main class="stage">

  <section class="card card--front" aria-label="Card front">
    <div class="front-pattern" role="img" aria-label="Faint repeating brand emblem pattern on black"></div>
    <div class="front-identity">
      <div class="wordmark">
        <span class="wordmark__square"></span>
        <span class="wordmark__name">Rijwielwerkplaats<br>Vanhoutte</span>
      </div>
      <p class="slogan">Herstellingen van alle merken.</p>
    </div>
  </section>

  <section class="card card--back" aria-label="Card back">
    <div class="owners">
      <p class="owners__label">Shop owner:</p>
      <p class="owners__names">Bart Vanhoutte &amp; Marieke Segers</p>
    </div>

    <span class="accent-bar"></span>
    <div class="company">
      <p class="company__name">Rijwielwerkplaats Vanhoutte</p>
      <p class="company__role">General Manager</p>
    </div>

    <ul class="contact">
      <li class="contact__item">
        <svg class="contact__icon" viewBox="0 0 12 12"><path fill="#e8243f" d="M2.5 .8 4.3 2.9 3.3 4.3c.7 1.5 1.9 2.7 3.4 3.4l1.4-1 2.1 1.8-.9 1.9C4.8 10.4 1.6 7.2.6 1.7z"/></svg>
        +32471902368
      </li>
      <li class="contact__item">
        <svg class="contact__icon" viewBox="0 0 12 12"><rect x=".5" y="2" width="11" height="8" fill="#e8243f"/><path d="M1 2.6 6 6.6l5-4" stroke="#fff" stroke-width="1" fill="none"/></svg>
        info@rijwielwerkplaats-vanhoutte.be
      </li>
      <li class="contact__item">
        <svg class="contact__icon" viewBox="0 0 12 12"><circle cx="6" cy="6" r="5.5" fill="#e8243f"/><path d="M.5 6h11M6 .5c-2.5 3-2.5 8 0 11M6 .5c2.5 3 2.5 8 0 11" stroke="#fff" stroke-width=".8" fill="none"/></svg>
        www.rijwielwerkplaats-vanhoutte.be
      </li>
    </ul>
    <p class="address">Kerkweg 46 9940 Bellebeke</p>

    <div class="back-mark">
      <span class="back-mark__square"></span>
      <span class="back-mark__name">Rijwielwerkplaats Vanhoutte</span>
    </div>
  </section>

</main>
</body>
</html>
```